Business Card Design - Photographer

I am a landscape photographer and I require a business card design. 

I require two designs:
1)  a double sided business card
 and
b)  a single sided business card 

The single sided design can either be the same as the double sided (with just one side having all the information)....or it can be an entire new design. Its up to you.

My corporate colours are (CMYK):

Blue   69, 32, 0, 0
Grey  72,  64,  47,  31
Green  32,  2,  91,  0
Yellow   0, 19, 92, 0
Orange  0, 39, 75, 0

Colour space in final file should be in CMYK.

The details that need to be included on the card:

- Use the provided Logo
- Name: Wiktor Baranowski
- Email:   sales@vistalumeworks.com.au
- Website:    vistalumeworks.com.au
- Twitter:    twitter.com/vistalumeworks
- Facebook:   facebook.com/vistalumeworks
- Mobile  0417 539 662

Please use the attached template to design the logo to the specified size, including the marked bleed lines. I have also attached my logo in PNG (transparent background) and ai format for you to use.

The final file should be:
- Photoshop version with layers so I can edit the name/text etc. All non vector files should be high resolution at 1039 x 697 pixels at 300 dpi.

I also require a file as:
- Vector based PDF

Anyway questions please contact me.

Thank you

Industry/Entity Type

Landscape

Logo styles of interest
Pictorial/Combination Logo
Abstract Logo
Wordmark Logo
Lettermark Logo
Requirements
Must have
• The details that need to be included on the card:

- Use the provided Logo
- Name: Wiktor Baranowski
- Email: sales@vistalumeworks.com.au
- Website: vistalumeworks.com.au
- Twitter: twitter.com/vistalumeworks
- Facebook: facebook.com/vistalumeworks
- Mobile 0417 539 662

```html
<!DOCTYPE html>
<html lang="en">
<head>
<meta charset="utf-8">
<title>Vistalume Works – Business Card</title>
<link rel="stylesheet" href="https://fonts.googleapis.com/css2?family=Cinzel:wght@500&family=Source+Sans+3:wght@400;700&display=swap">
<style>
  :root {
    --backdrop: #2f3534;
    --card: #ffffff;
    --ink: #3a3d4c;
    --blue: #3d8fce;
    --green: #b5cf3a;
    --slate: #3a3d4c;
    --white: #ffffff;
  }
  * { margin: 0; padding: 0; box-sizing: border-box; }
  html, body { width: 987px; height: 1200px; overflow: hidden; }
  body {
    background: var(--backdrop);
    position: relative;
    font-family: "Source Sans 3", "Helvetica Neue", Arial, sans-serif;
    color: var(--ink);
  }
  .card {
    position: absolute;
    background: var(--card);
    border-radius: 28px;
    overflow: hidden;
  }
  .card--front { left: 88px; top: 117px; width: 790px; height: 450px; }
  .card--back  { left: 92px; top: 637px; width: 788px; height: 450px; }

  .wave { position: absolute; left: 0; top: 0; width: 100%; height: 100%; }
  .wave .band-blue  { fill: var(--blue); }
  .wave .band-slate { fill: var(--slate); }
  .wave .band-green { fill: var(--green); }

  .brand-mark {
    position: absolute;
    border-radius: 50%;
    background: var(--slate);
  }
  .card--front .brand-mark { left: 156px; top: 52px; width: 144px; height: 144px; }
  .card--back  .brand-mark { left: 289px; top: 28px; width: 210px; height: 210px; }

  .brand-name {
    position: absolute;
    font-family: "Cinzel", "Times New Roman", serif;
    font-weight: 500;
    color: var(--ink);
    white-space: nowrap;
    text-align: center;
    line-height: 1;
  }
  .card--front .brand-name { left: 34px; width: 388px; top: 216px; font-size: 33px; }
  .card--back  .brand-name { left: 0; width: 100%; top: 266px; font-size: 50px; }

  .brand-rule { position: absolute; height: 2px; background: var(--ink); }
  .card--front .brand-rule { left: 34px; width: 388px; top: 254px; }
  .card--back  .brand-rule { left: 111px; width: 564px; top: 322px; }

  .holder { position: absolute; left: 469px; top: 52px; }
  .holder__name { font-size: 30px; font-weight: 700; line-height: 1; }
  .holder__role { font-size: 18px; margin-top: 6px; line-height: 1; }

  .contacts, .socials { position: absolute; list-style: none; font-size: 19px; line-height: 30px; }
  .contacts { left: 465px; top: 196px; color: var(--ink); }
  .socials { left: 42px; top: 376px; color: var(--white); }
  .contacts b, .socials b { font-weight: 700; }

  .web-address {
    position: absolute; left: 0; width: 100%; top: 396px;
    text-align: center; font-size: 26px; color: var(--ink); line-height: 1;
  }
</style>
</head>
<body>
  <section class="card card--front">
    <svg class="wave" viewBox="0 0 790 450" preserveAspectRatio="none" aria-hidden="true">
      <path class="band-blue" d="M0,313 C200,330 420,420 600,430 C700,436 760,428 790,420 L790,450 L0,450 Z"/>
      <path class="band-slate" d="M30,315 C250,330 450,400 620,405 C700,407 760,395 790,380 L790,405 C740,420 680,425 600,422 C430,415 250,340 30,315 Z"/>
      <path class="band-green" d="M240,336 C400,360 560,390 660,380 C720,374 760,360 790,342 L790,365 C740,385 690,396 640,398 C520,400 400,370 240,336 Z"/>
    </svg>

    <div class="brand-mark" aria-hidden="true"></div>
    <div class="brand-name">Vistalume Works</div>
    <div class="brand-rule"></div>

    <div class="holder">
      <p class="holder__name">Your Name</p>
      <p class="holder__role">Adminsitrator</p>
    </div>

    <ul class="contacts">
      <li><b>m</b> : 0417 539 662</li>
      <li><b>e</b> : sales@vistalumeworks.com.au</li>
      <li><b>w</b> : vistalumeworks.com.au</li>
    </ul>

    <ul class="socials">
      <li><b>t</b> : twitter.com/vistalumeworks</li>
      <li><b>f</b> : facebook.com/vistalumeworks</li>
    </ul>
  </section>

  <section class="card card--back">
    <div class="brand-mark" aria-hidden="true"></div>
    <div class="brand-name">Vistalume Works</div>
    <div class="brand-rule"></div>
    <p class="web-address">www.vistalumeworks.com.au</p>
  </section>
</body>
</html>
```